We are a doctors medical practice
I need the business card to be eye catching and memorable,
to reflect professionalism, yet also warmth and care

the numbers need to be easy to see, for the elderly

and the logo also in a location that is large enough to see and be eye catching

Back of card:
opening hours:
Mon- Fri 8.30am to 6pm
Sat 9am to 4pm

rows for appontments, date and time
Updates

HiĀ 

Modification to company name

BROOKVALE KINDRED HEALTH MEDICAL PRACTICE

Thanks
Marla

Reason: I am look for a unique design that also fulfils the design brief

I have attempted to post a .eps and .ai file of the logo

Target Market(s)

needs to appeal to the majority, mainly adults

Industry/Entity Type

Medical

Contact Information for Business Card

company name: Brookvale Kindred Health Medical Practice
Name: Dr Marla Tobrik-Vey
Qualifications: MBBS, Bsci(med), FRACGP, DCH, SH&FPA, Dip Derm
Address: Shop 3/41-43 Corrow St, Fairfield 2165
Ph: 02 9184 3025
Fax: 02 9318 6042

Requirements
Nice to have
• I like balance
gold/ silver incorporated, as well as the other colours in the logo- but not limited to these colours
a "medical" feel
Should not have
• dark or strong colours

```html
<!DOCTYPE html>
<html lang="en">
<head>
<meta charset="utf-8">
<title>Brookvale Kindred Health Medical Practice – Business Card</title>
<link rel="stylesheet" href="https://fonts.googleapis.com/css2?family=Open+Sans:wght@400;600;700;800&display=swap">
<style>
  :root {
    --page-bg: #e4e8ea;
    --card-white: #ffffff;
    --gold: #e8c11e;
    --orange: #f08a1c;
    --green: #a5c73a;
    --blue: #1b6fc4;
    --blue-dark: #1559a8;
    --band-blue: #1a86d0;
    --grey-text: #7c7c7c;
    --ink: #2b2b2b;
    --back-grey-top: #f4f4f4;
    --back-grey-bottom: #dcdcdc;
    --rule: #555555;
  }
  * { box-sizing: border-box; margin: 0; padding: 0; }
  html, body { width: 1200px; height: 900px; overflow: hidden; }
  body {
    background: var(--page-bg);
    font-family: "Open Sans", Arial, sans-serif;
    display: flex;
    align-items: center;
    justify-content: center;
    gap: 40px;
  }
  .card {
    position: relative;
    width: 540px;
    height: 330px;
    overflow: hidden;
    box-shadow: 0 6px 18px rgba(0,0,0,0.18);
  }
  .card-art { position: absolute; inset: 0; }

  /* Front */
  .card-front { background: var(--card-white); }
  .doctor-name {
    position: absolute; left: 22px; top: 16px;
    font-size: 23px; font-weight: 700; color: var(--blue-dark);
  }
  .qualifications {
    position: absolute; left: 22px; top: 54px;
    font-size: 13px; font-weight: 600; color: var(--grey-text); line-height: 1.45;
  }
  .brand-mark {
    position: absolute; left: 248px; top: 86px;
    display: flex; align-items: center; gap: 8px;
  }
  .brand-dot {
    width: 46px; height: 46px; border-radius: 50%;
    border: 4px solid var(--blue);
  }
  .brand-name {
    font-size: 13px; font-weight: 700; color: var(--blue); line-height: 1.2;
  }
  .practice-name {
    position: absolute; left: 34px; top: 170px;
    font-size: 19px; font-weight: 800; color: var(--blue);
    transform: rotate(-4deg); transform-origin: left center;
    white-space: nowrap;
  }
  .contact-list {
    position: absolute; right: 20px; top: 198px;
    list-style: none;
  }
  .contact-list li {
    display: flex; align-items: center; gap: 8px;
    font-size: 16px; font-weight: 600; color: var(--ink);
    margin-bottom: 5px;
  }
  .contact-list svg { width: 18px; height: 18px; }
  .address {
    position: absolute; right: 20px; top: 272px;
    font-size: 16px; font-weight: 600; color: var(--ink);
    transform: rotate(-6deg); transform-origin: right center;
    white-space: nowrap;
  }

  /* Back */
  .card-back {
    background: linear-gradient(160deg, var(--back-grey-top), var(--back-grey-bottom));
  }
  .hours-band {
    position: absolute; left: 0; top: 0; bottom: 0; width: 56px;
    background: var(--band-blue);
  }
  .hours-text {
    position: absolute; left: 28px; top: 165px;
    transform: translate(-50%, -50%) rotate(-90deg);
    white-space: nowrap; text-align: center;
    color: #fff; font-size: 11.5px; font-weight: 600; line-height: 1.35;
  }
  .hours-text strong { font-weight: 800; }
  .watermark {
    position: absolute; left: 210px; top: 75px;
    display: flex; align-items: center; gap: 10px; opacity: 0.18;
  }
  .watermark .brand-dot { width: 120px; height: 120px; border-width: 8px; }
  .watermark .brand-name { font-size: 16px; }
  .appointments-label {
    position: absolute; left: 80px; top: 18px;
    font-size: 13px; font-weight: 700; color: #3a3a3a;
  }
  .datetime-label {
    position: absolute; right: 22px; top: 38px;
    font-size: 12px; font-weight: 700; color: #3a3a3a;
  }
  .appointment-rows {
    position: absolute; left: 80px; right: 22px; top: 44px;
    list-style: none;
  }
  .appointment-rows li {
    height: 27px;
    border-bottom: 1.5px dotted var(--rule);
  }
</style>
</head>
<body>

  <section class="card card-front" aria-label="Business card front">
    <svg class="card-art" viewBox="0 0 540 330" preserveAspectRatio="none" aria-hidden="true">
      <path d="M0 0 H540 V0 C430 22 300 62 0 118 Z" fill="var(--gold)"/>
      <path d="M0 118 C300 62 430 22 540 0 V8 C430 30 300 72 0 128 Z" fill="var(--orange)"/>
      <path d="M540 178 C420 220 260 280 120 330 H540 Z" fill="var(--green)"/>
      <path d="M540 168 C420 210 260 272 100 330 H120 C260 280 420 220 540 178 Z" fill="var(--orange)"/>
      <path d="M0 304 C30 312 50 320 60 330 H0 Z" fill="var(--orange)"/>
    </svg>

    <h1 class="doctor-name">Dr Marla Tobrik-Vey</h1>
    <p class="qualifications">MBBS, Bsci(med), FRACGP,<br>DCH, SH&amp;FPA, Dip Derm</p>

    <div class="brand-mark">
      <span class="brand-dot"></span>
      <span class="brand-name">Brookvale<br>Kindred Health</span>
    </div>

    <h2 class="practice-name">BROOKVALE KINDRED HEALTH MEDICAL PRACTICE</h2>

    <ul class="contact-list">
      <li>
        <svg viewBox="0 0 20 20" aria-label="Phone"><path d="M2 7 C2 3 18 3 18 7 V9 H14 V7 H6 V9 H2 Z M5 10 H15 L17 17 H3 Z" fill="var(--ink)"/><circle cx="10" cy="13.5" r="2" fill="var(--green)"/></svg>
        02 9184 3025
      </li>
      <li>
        <svg viewBox="0 0 20 20" aria-label="Fax"><rect x="3" y="2" width="14" height="16" rx="2" fill="none" stroke="var(--ink)" stroke-width="2"/><rect x="6" y="5" width="8" height="4" fill="var(--ink)"/><rect x="6" y="11" width="8" height="4" fill="var(--ink)"/></svg>
        02 9318 6042
      </li>
    </ul>

    <p class="address">Shop 3/41-43 Corrow St, Kindale 2318</p>
  </section>

  <section class="card card-back" aria-label="Business card back">
    <div class="watermark" aria-hidden="true">
      <span class="brand-dot"></span>
      <span class="brand-name">Brookvale<br>Kindred Health</span>
    </div>

    <div class="hours-band">
      <p class="hours-text"><strong>OPENING HOURS:</strong> Mon- Fri 8.30am to 6pm<br>Sat 9am to 4pm</p>
    </div>

    <h3 class="appointments-label">Appontments</h3>
    <span class="datetime-label">Date &amp; Time</span>

    <ol class="appointment-rows">
      <li></li><li></li><li></li><li></li><li></li>
      <li></li><li></li><li></li><li></li><li></li>
    </ol>
  </section>

</body>
</html>
```